A start-up named "lumerova" - a clinical research organization needs a new PowerPoint design

We need a new PowerPoint Design (incl. business card and stationery design) for an early-stage start-up named "lumerova" seeking to build an ecosystem/ strategic partner alliances or consortium of committed and active collaborators to guide important components of the clinical trial.

Our ultimate goal is to avoid false neutrals – therapies that have not been and may never be evaluated in clinical trials due to the costs and/ or complexity.

The final design should highlight our patient-centric approach, innovative study design supported with the novel AI platform to make a stronger impact on patient lives.

Please see the attached brief for more details.
Updates

Requesting the proposals on color-coding, business-card designs, clinical research visuals, and icons as well as stationery design.

Target Market(s)

Pharma/ Biotech Executives
Medical Institutions
Clinical Trial Participants (Patients)

Colors
e34398

Requirements
Must have
• Use the Color Version of purple/ magenta logo

```html
<!DOCTYPE html>
<html lang="en">
<head>
<meta charset="utf-8">
<title>Lumerova – Stationery &amp; Business Card Design</title>
<link rel="stylesheet" href="https://fonts.googleapis.com/css2?family=Ubuntu:wght@400;500;700&family=Raleway:wght@300&display=swap">
<style>
:root{
  --bg:#e6e6e6;
  --paper:#f4f4f4;
  --paper-white:#fafafa;
  --brand:#c8177a;
  --brand-line:#d4237f;
  --brand-soft:#f1dbe6;
  --ink:#222;
  --muted:#666;
  --caption:#8a8a8a;
  --rule:#9a9a9a;
}
*{margin:0;padding:0;box-sizing:border-box}
html,body{width:1200px;height:633px;overflow:hidden}
body{background:var(--bg);position:relative;font-family:"Ubuntu",sans-serif;color:var(--ink)}
.sheet{position:absolute;background:var(--paper);overflow:hidden}
.wordmark{position:absolute;font-family:"Ubuntu",sans-serif;font-weight:500;color:var(--brand);line-height:1;white-space:nowrap}
.decor{position:absolute;right:0;bottom:0;background:linear-gradient(135deg,rgba(241,219,230,0) 0%,var(--brand-soft) 60%,#ecd0de 100%)}
.small{position:absolute;line-height:1.25;white-space:nowrap}
.small b{font-weight:700}

/* envelope */
.envelope{left:243px;top:134px;width:259px;height:129px}
.envelope .wordmark{left:17px;top:16px;font-size:17px}
.envelope .address{left:17px;top:42px;font-size:4.4px}
.envelope .decor{width:88px;height:84px}

/* letterhead */
.letterhead{left:531px;top:133px;width:245px;height:348px}
.letterhead .wordmark{left:18px;top:20px;font-size:17px}
.letterhead .rule{position:absolute;left:0;right:0;top:41px;height:1px;background:var(--brand-line)}
.letterhead .small{top:18px;font-size:3.3px}
.letterhead .col-a{left:117px}
.letterhead .col-b{left:153px}
.letterhead .col-c{left:194px}
.letterhead .decor{width:109px;height:116px}

/* folder */
.folder{left:808px;top:133px;width:254px;height:366px}
.folder .wordmark{left:29px;top:46px;font-size:37px}
.folder .url{position:absolute;left:97px;top:342px;font-size:7px;color:var(--brand)}
.folder .decor{width:121px;height:177px}

/* notebook cover */
.notebook{left:366px;top:301px;width:133px;height:184px}
.notebook .wordmark{left:14px;top:54px;font-size:20px}
.notebook .url{position:absolute;left:50px;top:173px;font-size:3.8px;color:var(--brand)}
.notebook .decor{width:66px;height:88px}

/* business cards */
.card{width:102px;height:66px;background:var(--paper-white)}
.card-front{left:115px;top:311px}
.card-back{left:236px;top:310px}
.card .name{position:absolute;left:10px;top:14px;font-size:4.6px;font-weight:700;color:var(--brand)}
.card .title{left:10px;top:20px;font-size:3.4px}
.card .title span{color:var(--muted);font-size:2.8px}
.card .wordmark{font-size:6.5px;top:13px;left:63px}
.card .contacts{left:10px;top:36px;font-size:2.5px}
.card .company{left:63px;top:41px;font-size:2.9px}
.card .line{position:absolute;height:1px;background:var(--brand-line)}
.card-front .line.top{left:70px;right:0;top:21px}
.card-front .line.bottom{left:0;width:44px;top:61px}
.card-back .name{left:8px;top:14px}
.card-back .title{left:8px;top:23px}
.card-back .contacts{left:8px;top:37px}
.card-back .contacts.web{top:53px}
.card-back .wordmark{left:66px;top:12px}
.card-back .company{left:65px;top:43px}
.card-back .line.top{left:8px;right:0;top:21px}
.card-back .line.bottom{left:0;width:42px;top:49px}

/* caption band */
.caption-band{position:absolute;left:0;right:0;top:563px;height:70px;background:#fff;display:flex;align-items:center}
.caption-band .rule{flex:1;height:1px;background:var(--rule)}
.caption-band h1{margin:0 24px 0 28px;font-family:"Raleway",sans-serif;font-weight:300;font-size:28px;letter-spacing:.2em;color:var(--caption);white-space:nowrap;line-height:1}
</style>
</head>
<body>

<section class="sheet envelope">
  <div class="wordmark">lumerova</div>
  <div class="small address"><b>Lumerova GmbH</b><br>Street name 1<br>9999 City name<br>Switzerland</div>
  <div class="decor" role="img" aria-label="Soft pink decorative brand pattern area"></div>
</section>

<section class="sheet letterhead">
  <div class="wordmark">lumerova</div>
  <div class="small col-a"><b>Lumerova GmbH</b><br>Street name 1<br>9999 City name<br>Switzerland</div>
  <div class="small col-b">O: +41 (0)44 555 01 00<br>P: +41 (0)44 555 01 09<br>M: +41 (0)79 555 01 21<br>F: +41 (0)44 555 01 01</div>
  <div class="small col-c">name.surname@lumerova.ch<br>www.lumerova.ch</div>
  <div class="rule"></div>
  <div class="decor" role="img" aria-label="Soft pink decorative brand pattern area"></div>
</section>

<section class="sheet folder">
  <div class="wordmark">lumerova</div>
  <div class="decor" role="img" aria-label="Soft pink decorative brand pattern area"></div>
  <div class="url">www.lumerova.ch</div>
</section>

<section class="sheet card card-front">
  <div class="name">Name Surname</div>
  <div class="small title"><b>PhD</b><br><span>Managing Partner</span></div>
  <div class="wordmark">lumerova</div>
  <div class="line top"></div>
  <div class="small contacts">O: +41 (0)44 555 01 00<br>P: +41 (0)44 555 01 09<br>M: +41 (0)79 555 01 21<br>F: +41 (0)44 555 01 01<br><br>name.surname@lumerova.ch<br>www.lumerova.ch</div>
  <div class="small company"><b>Lumerova GmbH</b><br>Street name 1<br>9999 City name<br>Switzerland</div>
  <div class="line bottom"></div>
</section>

<section class="sheet card card-back">
  <div class="name">Name Surname</div>
  <div class="wordmark">lumerova</div>
  <div class="line top"></div>
  <div class="small title"><b>PhD</b><br><span>Managing Partner</span></div>
  <div class="small contacts">O: +41 (0)44 555 01 00<br>P: +41 (0)44 555 01 09<br>M: +41 (0)79 555 01 21<br>F: +41 (0)44 555 01 01</div>
  <div class="line bottom"></div>
  <div class="small company"><b>Lumerova GmbH</b><br>Street name 1<br>9999 City name<br>Switzerland</div>
  <div class="small contacts web">name.surname@lumerova.ch<br><b>www.lumerova.ch</b></div>
</section>

<section class="sheet notebook">
  <div class="wordmark">lumerova</div>
  <div class="decor" role="img" aria-label="Soft pink decorative brand pattern area"></div>
  <div class="url">www.lumerova.ch</div>
</section>

<footer class="caption-band">
  <div class="rule"></div>
  <h1>STATIONERY &amp; BUSINESS CARD DESIGN</h1>
  <div class="rule"></div>
</footer>

</body>
</html>
```